SUPPLEMENT BOTTLE LABEL: TOLVERIN

We need a NEW FRESH look to her labels. Something contemporary, clean and professional. The colors need to remain the same but everything else can change, even the logo.

THE CURRENT LABEL IS ATTACHED IN PDF FORMAT

Target Market(s)

WOMEN BETWEEN 35-60

Requirements
Must have
• SAME COLORS
• FRESH
• CLEAN

```html
<!DOCTYPE html>
<html lang="en">
<head>
<meta charset="UTF-8">
<title>Vital Renew Cleanse Label – Tolverin</title>
<link rel="stylesheet" href="https://fonts.googleapis.com/css2?family=Kaushan+Script&family=Righteous&family=Oswald:wght@600&family=Patrick+Hand&display=swap">
<style>
  :root {
    --stage: #e6e3ec;
    --navy-deep: #07152c;
    --navy: #0f2550;
    --royal: #2446a8;
    --green: #5da53a;
    --green-dark: #2f6a1d;
    --white: #ffffff;
    --cream: #f4ecd8;
  }
  * { margin: 0; padding: 0; box-sizing: border-box; }
  html, body { width: 1200px; height: 1200px; overflow: hidden; }
  body { background: var(--stage); position: relative; }

  .label {
    position: absolute;
    left: 170px; top: 85px;
    width: 860px; height: 1030px;
    overflow: hidden;
    background:
      linear-gradient(90deg, rgba(0,0,0,.45) 0%, rgba(0,0,0,0) 18%, rgba(0,0,0,0) 82%, rgba(0,0,0,.45) 100%),
      radial-gradient(ellipse 55% 50% at 50% 45%, var(--royal) 0%, var(--navy) 55%, var(--navy-deep) 100%);
    color: var(--white);
    text-align: center;
  }
  .label-corners { position: absolute; inset: 0; width: 100%; height: 100%; }

  .brand-name {
    position: absolute; top: 120px; left: 0; right: 0;
    font-family: 'Kaushan Script', cursive;
    font-size: 112px; line-height: 1;
    color: var(--white);
  }
  .divider-dots {
    position: absolute; top: 290px; left: 70px; right: 70px;
    height: 14px;
    display: flex; justify-content: space-between; align-items: center;
  }
  .divider-dots span { width: 5px; height: 5px; border-radius: 50%; background: var(--cream); }
  .divider-dots span.big { width: 9px; height: 9px; }
  .divider-dots span.mid { width: 7px; height: 7px; }

  .product-type {
    position: absolute; top: 335px; left: 0; right: 0;
    font-family: 'Righteous', sans-serif;
    font-size: 92px; line-height: 1; letter-spacing: 3px;
    color: var(--navy);
    -webkit-text-stroke: 4px var(--white);
    paint-order: stroke fill;
  }
  .flavor {
    position: absolute; top: 430px; left: 0; right: 0;
    font-family: 'Kaushan Script', cursive;
    font-size: 110px; line-height: 1;
  }
  .flavor-note {
    position: absolute; top: 570px; left: 0; right: 0;
    font-family: 'Oswald', sans-serif; font-weight: 600;
    font-size: 29px;
  }
  .product-info {
    position: absolute; top: 648px; left: 40px; right: 40px;
    font-family: 'Patrick Hand', cursive;
    font-size: 29px; line-height: 45px;
    text-transform: uppercase;
  }
  .net-weight {
    position: absolute; top: 868px; left: 0; right: 0;
    display: flex; justify-content: center; align-items: center; gap: 14px;
    font-family: 'Patrick Hand', cursive;
    font-size: 34px;
  }
  .net-weight::before, .net-weight::after {
    content: ""; width: 65px; height: 2px; background: var(--white);
  }
</style>
</head>
<body>
  <section class="label" aria-label="Vital Renew Cleanse Chocolate supplement label">
    <svg class="label-corners" viewBox="0 0 860 1030" preserveAspectRatio="none" aria-hidden="true">
      <defs>
        <linearGradient id="corner-green" x1="0" y1="0" x2="0" y2="1">
          <stop offset="0" stop-color="var(--green-dark)"/>
          <stop offset="1" stop-color="var(--green)"/>
        </linearGradient>
      </defs>
      <polygon points="0,640 0,1030 190,1030" fill="url(#corner-green)"/>
      <line x1="0" y1="640" x2="190" y2="1030" stroke="var(--white)" stroke-width="5"/>
      <polygon points="860,630 860,1030 650,1030" fill="url(#corner-green)"/>
      <line x1="860" y1="630" x2="650" y2="1030" stroke="var(--white)" stroke-width="5"/>
    </svg>

    <h1 class="brand-name">Vital Renew</h1>

    <div class="divider-dots" aria-hidden="true">
      <span></span><span></span><span></span><span></span><span></span><span></span><span></span><span></span><span></span><span class="mid"></span><span class="mid"></span><span class="mid"></span><span class="mid"></span><span class="mid"></span><span class="mid"></span><span class="big"></span><span class="big"></span><span class="big"></span><span class="mid"></span><span class="mid"></span><span class="mid"></span><span class="mid"></span><span class="mid"></span><span class="mid"></span><span></span><span></span><span></span><span></span><span></span><span></span><span></span><span></span><span></span>
    </div>

    <h2 class="product-type">CLEANSE</h2>
    <p class="flavor">Chocolate</p>
    <p class="flavor-note">with other natural flavors</p>

    <p class="product-info">
      Collagen, multivitamin, mineral &amp;<br>
      herbal dietary supplement powder<br>
      Notice: use this product as a food supplement only.<br>
      Do not use for weight reduction.
    </p>

    <p class="net-weight">NET WT. 1.21 LBS (551.2 G)</p>
  </section>
</body>
</html>
```